Design a book cover
TItle: Where Would Mercy Stand?
Suggested graphic: Jesus holding a gun
Subtitle: A public defender's views on the death penalty
Author Name: Gordon Maskelyne

```html
<!DOCTYPE html>
<html lang="en">
<head>
<meta charset="UTF-8">
<title>Where Would Mercy Stand? — Book Cover</title>
<link href="https://fonts.googleapis.com/css2?family=Bebas+Neue&family=Cinzel:wght@400;500&display=swap" rel="stylesheet">
<style>
  :root {
    --cover-brown: #6d3320;
    --cover-brown-light: #783a25;
    --cover-brown-dark: #5f2b1a;
    --tan: #d6b577;
    --artwork-dark: #2a2524;
    --artwork-mid: #4a4442;
  }
  html, body {
    margin: 0;
    padding: 0;
    width: 800px;
    height: 1200px;
    overflow: hidden;
    background: var(--cover-brown);
  }
  .book-cover {
    position: relative;
    width: 800px;
    height: 1200px;
    overflow: hidden;
    background:
      radial-gradient(ellipse at 50% 45%, var(--cover-brown-light) 0%, var(--cover-brown) 60%, var(--cover-brown-dark) 100%);
    color: var(--tan);
    text-align: center;
  }
  .cover-title {
    position: absolute;
    top: 62px;
    left: 0;
    width: 100%;
    margin: 0;
    font-family: "Bebas Neue", "Oswald", sans-serif;
    font-weight: 400;
    font-size: 156px;
    line-height: 128px;
    letter-spacing: 1px;
    text-transform: uppercase;
  }
  .cover-title span { display: block; }
  .cover-subtitle {
    position: absolute;
    top: 414px;
    left: 0;
    width: 100%;
    margin: 0;
    font-family: "Cinzel", "Times New Roman", serif;
    font-weight: 400;
    font-size: 27px;
    line-height: 34px;
    letter-spacing: 1px;
    text-transform: uppercase;
  }
  .cover-subtitle span { display: block; }
  .cover-artwork {
    position: absolute;
    top: 544px;
    left: 231px;
    width: 348px;
    height: 430px;
  }
  .cover-author {
    position: absolute;
    top: 1070px;
    left: 0;
    width: 100%;
    margin: 0;
    font-family: "Bebas Neue", "Oswald", sans-serif;
    font-weight: 400;
    font-size: 58px;
    line-height: 64px;
    letter-spacing: 7px;
    text-transform: uppercase;
  }
</style>
</head>
<body>
  <main class="book-cover">
    <h1 class="cover-title">
      <span>Where Would</span>
      <span>Mercy Stand?</span>
    </h1>
    <p class="cover-subtitle">
      <span>A Public Defender's Views on</span>
      <span>the Death Penalty</span>
    </p>
    <svg class="cover-artwork" viewBox="0 0 348 430" role="img" aria-label="Illustration of a black Holy Bible with a handgun resting on top of it">
      <defs>
        <linearGradient id="artwork-tone" x1="0" y1="0" x2="1" y2="1">
          <stop offset="0" stop-color="var(--artwork-mid)"/>
          <stop offset="1" stop-color="var(--artwork-dark)"/>
        </linearGradient>
      </defs>
      <rect x="0" y="0" width="348" height="430" rx="8" fill="url(#artwork-tone)"/>
    </svg>
    <p class="cover-author">Gordon Maskelyne</p>
  </main>
</body>
</html>
```